BrindleStaffing Business Card Design

We are a staffing company finding positions for dedicated nurses and physicians.

Target Market(s)

Business Professionals

Industry/Entity Type

Staffing

Contact Information for Business Card

Gordon Pratley
Chairman
417 39th Avenue South
SAINT PETERSBURG FL 33712
813-555-4172 Mobile
813-555-8036 Fax
gpratley@brindlestaffing.com
www.brindlestaffing.com

Font styles to use
Sans Serif

Colors
fbee3e
f04a50
f37122

Requirements
Must have
• Logo Attached, see colors below. We'd like to see Yellow, Orange and Red.

```html
<!DOCTYPE html>
<html lang="en">
<head>
<meta charset="utf-8">
<title>BrindleStaffing Business Card</title>
<link rel="stylesheet" href="https://fonts.googleapis.com/css2?family=Lato:wght@400&family=Nunito:wght@700;800&display=swap">
<style>
  :root {
    --backdrop: #e9e7e4;
    --brand-red: #f04a50;
    --brand-orange: #f37122;
    --brand-yellow: #fbee3e;
    --seal-fill: #f4f2ee;
    --ink-light: #ffffff;
    --wordmark: #f04a50;
  }
  html, body {
    margin: 0;
    width: 1200px;
    height: 900px;
    overflow: hidden;
    background: var(--backdrop);
  }
  .card {
    position: absolute;
    left: 150px;
    top: 171px;
    width: 900px;
    height: 558px;
    background: var(--brand-orange);
    overflow: hidden;
    box-shadow: 0 10px 30px rgba(0,0,0,0.18);
  }
  .card__panel {
    position: absolute;
    left: 0;
    top: 0;
    width: 609px;
    height: 100%;
    background: var(--brand-red);
  }
  .card__seal {
    position: absolute;
    left: 367px;
    top: 35px;
    width: 484px;
    height: 484px;
    border-radius: 50%;
    background: var(--seal-fill);
    display: flex;
    align-items: center;
    justify-content: center;
  }
  .wordmark {
    display: flex;
    align-items: center;
    gap: 10px;
    font-family: "Nunito", sans-serif;
    font-weight: 800;
    font-size: 48px;
    color: var(--wordmark);
    letter-spacing: -0.5px;
    white-space: nowrap;
  }
  .wordmark__dot {
    width: 26px;
    height: 26px;
    border-radius: 50%;
    background: var(--brand-yellow);
    flex: none;
  }
  .card__identity {
    position: absolute;
    left: 54px;
    top: 70px;
    z-index: 2;
    color: var(--ink-light);
  }
  .card__name {
    margin: 0;
    font-family: "Nunito", sans-serif;
    font-weight: 700;
    font-size: 36px;
    line-height: 48px;
  }
  .card__title {
    margin: 4px 0 0;
    font-family: "Lato", sans-serif;
    font-size: 25px;
    line-height: 33px;
  }
  .card__address, .card__contacts {
    position: absolute;
    left: 54px;
    margin: 0;
    padding: 0;
    list-style: none;
    font-family: "Lato", sans-serif;
    font-size: 25px;
    line-height: 33px;
    color: var(--ink-light);
    z-index: 2;
  }
  .card__address { top: 248px; font-style: normal; }
  .card__contacts { top: 372px; }
  .contact {
    display: flex;
    align-items: center;
    gap: 7px;
    white-space: nowrap;
  }
  .contact__icon {
    width: 22px;
    height: 22px;
    flex: none;
    fill: var(--ink-light);
  }
  .contact__cut { fill: var(--brand-red); }
  .contact__line { fill: none; stroke: var(--brand-red); stroke-width: 1.8; }
</style>
</head>
<body>
  <div class="card">
    <div class="card__panel"></div>
    <div class="card__seal">
      <span class="wordmark"><span class="wordmark__dot"></span>BrindleStaffing</span>
    </div>

    <div class="card__identity">
      <h1 class="card__name">Gordon Pratley</h1>
      <p class="card__title">Chairman</p>
    </div>

    <address class="card__address">
      417 39th Avenue South<br>
      SAINT PETERSBURG<br>
      FL 33712
    </address>

    <ul class="card__contacts">
      <li class="contact">
        <svg class="contact__icon" viewBox="0 0 24 24" aria-hidden="true">
          <path d="M3 8c0-2 3-4 9-4s9 2 9 4v2h-5V8H8v2H3z"/>
          <path d="M6 11h12l2 8H4z"/>
          <circle class="contact__cut" cx="12" cy="15" r="2.2"/>
        </svg>
        813-555-4172 Mobile
      </li>
      <li class="contact">
        <svg class="contact__icon" viewBox="0 0 24 24" aria-hidden="true">
          <path d="M7 3h10v6H7z"/>
          <path d="M3 9h18v9H3z"/>
          <path d="M7 14h10v7H7z"/>
          <path class="contact__line" d="M9 17h6"/>
        </svg>
        813-555-8036 Fax
      </li>
      <li class="contact">
        <svg class="contact__icon" viewBox="0 0 24 24" aria-hidden="true">
          <path d="M3 6h18v12H3z"/>
          <path class="contact__line" d="M3 6l9 7 9-7"/>
        </svg>
        gpratley@brindlestaffing.com
      </li>
      <li class="contact">
        <svg class="contact__icon" viewBox="0 0 24 24" aria-hidden="true">
          <circle cx="12" cy="12" r="9"/>
          <path class="contact__line" d="M8 7c2 1 3 3 1 5s0 4 2 5M15 5c-1 2 1 3 3 3M16 14c1 1 2 2 1 4"/>
        </svg>
        www.brindlestaffing.com
      </li>
    </ul>
  </div>
</body>
</html>
```